Business card design for new eCommerce site focusing on integrity and strong businsess tactics

We need a business card that will stand out and be memorable. Something with color that matches our company logo colors. Think high end version of Pactivo. There are 2 logos provided. The parent company is called Amber Ledge Partners and we are presenting a new and very exciting eCommerce site called BrightHarborTrade.example.

Target Market(s)

Our target markets are in the Activities, Food and Beverage, Health and Beauty

Industry/Entity Type

Marketing

Contact Information for Business Card

We have 4 members that need cards...I will provide all info to the winner of the design contest
Business Address is
4870 West 63rd Avenue, Suite C207
Phoenix AZ 85731

Font styles to use
Serif
Sans Serif

Colors

Designer to choose colors to be used in the design.

Requirements
Must have
• The card must be memorable...should be unique in design but must exude integrity and be playful .
• I have provided several colors or our parent company...please feel free to use which ever
Nice to have
• I will leave this up to you. Feel free to use other images of your choosing that wraps around our client.....Activities, Dining, Health, Beauty
Should not have
• just dont be boring

```html
<!DOCTYPE html>
<html lang="en">
<head>
<meta charset="utf-8">
<title>BrightHarborTrade.example – Business Card</title>
<link rel="stylesheet" href="https://fonts.googleapis.com/css2?family=Questrial&family=Roboto+Condensed:wght@400;700&family=Arimo:wght@700&display=swap">
<style>
  :root {
    --page-bg: #e6e7e9;
    --paper: #f3f3f3;
    --ink: #4a4a4a;
    --brand-green: #7bc142;
    --brand-blue: #2b7db8;
    --back-light: #41bcd9;
    --back-deep: #2b7db0;
    --lime: #a9cc45;
    --white: #ffffff;
  }
  * { margin: 0; padding: 0; box-sizing: border-box; }
  html, body { width: 1200px; height: 960px; overflow: hidden; background: var(--page-bg); }
  .canvas { position: relative; width: 1200px; height: 960px; }

  .card {
    position: absolute;
    width: 600px;
    height: 342px;
    border-radius: 18px;
    overflow: hidden;
  }

  /* Front */
  .card-front { left: 302px; top: 131px; background: var(--paper); }
  .front-wave { position: absolute; inset: 0; }
  .brand {
    position: absolute; left: 48px; top: 62px;
    display: flex; align-items: center; gap: 10px;
  }
  .brand-dot { width: 18px; height: 18px; border-radius: 50%; background: var(--brand-green); }
  .brand-name {
    font-family: "Questrial", sans-serif;
    font-size: 25px; color: var(--brand-blue); letter-spacing: 0.2px;
  }
  .tagline {
    position: absolute; left: 76px; top: 96px;
    font-family: "Questrial", sans-serif;
    font-size: 13px; letter-spacing: 1.3px; color: var(--ink);
  }
  .address, .contacts {
    position: absolute; left: 48px;
    font-family: "Questrial", sans-serif;
    font-size: 14.5px; line-height: 19px; color: var(--ink);
    list-style: none;
  }
  .address { top: 156px; }
  .contacts { top: 219px; }
  .contacts li { display: flex; align-items: center; gap: 8px; }
  .contacts svg { width: 13px; height: 13px; fill: var(--brand-blue); flex: none; }
  .person {
    position: absolute; right: 50px; top: 247px; text-align: right;
    font-family: "Roboto Condensed", sans-serif; color: var(--white);
  }
  .person-name { font-size: 23px; font-weight: 700; line-height: 26px; }
  .person-role { font-size: 15px; font-weight: 400; line-height: 18px; }

  /* Back */
  .card-back {
    left: 299px; top: 490px;
    background: linear-gradient(135deg, var(--back-light) 0%, var(--back-deep) 45%, var(--back-deep) 100%);
  }
  .back-mark {
    position: absolute; left: 226px; top: 66px;
    width: 148px; height: 148px; border-radius: 50%;
    background: var(--lime);
    box-shadow: 0 0 0 3px var(--back-deep), 0 0 0 5px var(--lime);
  }
  .back-name {
    position: absolute; left: 0; right: 0; top: 222px; text-align: center;
    font-family: "Arimo", sans-serif; font-weight: 700;
    font-size: 34px; color: var(--lime);
  }
</style>
</head>
<body>
<main class="canvas">

  <section class="card card-front" aria-label="Card front">
    <svg class="front-wave" viewBox="0 0 600 342" aria-hidden="true">
      <path d="M540,0 C566,50 562,110 498,165 C425,228 352,262 362,342 L600,342 L600,0 Z" fill="var(--brand-green)"/>
      <path d="M540,0 C566,50 562,110 498,165 C425,228 352,262 362,342 L352,342 C338,262 410,205 486,150 C540,110 552,55 540,0 Z" fill="var(--brand-blue)"/>
      <path d="M352,342 C338,262 410,205 486,150 C540,110 552,55 540,0" fill="none" stroke="var(--white)" stroke-width="3"/>
    </svg>

    <div class="brand">
      <span class="brand-dot"></span>
      <span class="brand-name">BrightHarborTrade.example</span>
    </div>
    <p class="tagline">Activities-Dining-Health-Beauty</p>

    <address class="address">
      4870 West 63rd Avenue<br>
      Suite C207<br>
      Phoenix AZ 85731
    </address>

    <ul class="contacts">
      <li><svg viewBox="0 0 24 24"><path d="M6.6 10.8a15 15 0 0 0 6.6 6.6l2.2-2.2c.3-.3.7-.4 1-.2 1.1.4 2.3.6 3.6.6.6 0 1 .4 1 1V20c0 .6-.4 1-1 1A17 17 0 0 1 3 4c0-.6.4-1 1-1h3.5c.6 0 1 .4 1 1 0 1.3.2 2.5.6 3.6.1.3 0 .7-.2 1z"/></svg>602 555 0148</li>
      <li><svg viewBox="0 0 24 24"><path d="M7 1h10a2 2 0 0 1 2 2v18a2 2 0 0 1-2 2H7a2 2 0 0 1-2-2V3a2 2 0 0 1 2-2zm0 3v14h10V4zm5 15.5a1 1 0 1 0 0 2 1 1 0 0 0 0-2z"/></svg>602 555 0193</li>
      <li><svg viewBox="0 0 24 24"><path d="M2 5h20v14H2zm2 2v.5l8 5 8-5V7l-8 5z"/></svg>dana@brightharbortrade.example</li>
      <li><svg viewBox="0 0 24 24"><circle cx="12" cy="12" r="10"/></svg>www.brightharbortrade.example</li>
    </ul>

    <div class="person">
      <p class="person-name">DANA WHITFIELD</p>
      <p class="person-role">CEO/FOUNDER</p>
    </div>
  </section>

  <section class="card card-back" aria-label="Card back">
    <div class="back-mark"></div>
    <p class="back-name">Amber Ledge Partners</p>
  </section>

</main>
</body>
</html>
```